Request for Business Card Design

Hi. My name is Marlene, I am looking for a new business card design for my company, Quarrow Signal Instruments, LLC. I really like the design you did for Tarsel Venture and was hoping you could do something similar using our full logo and our mark. I am also open to any raised texture design using our mark. I have attached our full logo, which would need to be somewhere on the card, as well as the mark in both outline and full form, as well as our brand colors / guide. The card does not have to be white, as long as our logo and mark appear. I actually like darker colored business cards more, but am open to all options. If you are interested in working with me, please let me know. We would also take the business card design into letterhead design if you can do that.

```html
<!DOCTYPE html>
<html lang="en">
<head>
<meta charset="utf-8">
<title>Quarrow Signal Instruments – Business Card</title>
<link href="https://fonts.googleapis.com/css2?family=Open+Sans:wght@400;600;700&display=swap" rel="stylesheet">
<style>
  :root {
    --stage: #222223;
    --card-dark: #3b3b3d;
    --brand-blue: #1a96c0;
    --brand-blue-deep: #137ea3;
    --back-blue: #1b9bc6;
    --ink-light: #ffffff;
    --ink-soft: #e8e8e8;
    --chip: #f2f2f2;
  }
  * { box-sizing: border-box; margin: 0; padding: 0; }
  html, body { width: 1200px; height: 780px; overflow: hidden; background: var(--stage); }
  body { font-family: "Open Sans", Arial, sans-serif; position: relative; }

  .card {
    position: absolute;
    top: 240px;
    width: 525px;
    height: 300px;
    overflow: hidden;
  }
  .card--front { left: 45px; background: var(--card-dark); }
  .card--back { left: 630px; background: var(--back-blue); }

  /* Front: company name */
  .company {
    position: absolute;
    top: 40px;
    right: 40px;
    display: flex;
    align-items: center;
    gap: 12px;
  }
  .company__dot {
    width: 30px; height: 30px;
    border-radius: 50%;
    background: var(--brand-blue);
  }
  .company__name {
    font-weight: 700;
    font-size: 21px;
    color: var(--ink-light);
    letter-spacing: 0.5px;
    line-height: 1.15;
    text-transform: uppercase;
  }

  /* Front: person */
  .person {
    position: absolute;
    left: 60px;
    top: 132px;
    text-align: right;
    width: 150px;
  }
  .person__name {
    font-weight: 700;
    font-size: 33px;
    color: var(--brand-blue);
    line-height: 1;
  }
  .person__title {
    font-size: 15px;
    color: var(--ink-soft);
    margin-top: 4px;
  }
  .divider {
    position: absolute;
    left: 228px;
    top: 128px;
    width: 1px;
    height: 100px;
    background: #8a8a8c;
  }

  /* Front: contact list */
  .contacts {
    position: absolute;
    left: 246px;
    top: 136px;
    list-style: none;
  }
  .contacts li {
    display: flex;
    align-items: center;
    gap: 8px;
    font-size: 14px;
    color: var(--ink-light);
    line-height: 21px;
  }
  .contacts svg { width: 12px; height: 12px; flex: none; }

  /* Front: address band */
  .address-band {
    position: absolute;
    left: 0; right: 0; bottom: 0;
    height: 30px;
    background: var(--brand-blue);
    display: flex;
    align-items: center;
    padding-left: 30px;
    font-size: 14px;
    color: var(--ink-light);
  }
  .address-band__chip {
    position: absolute;
    right: 0; top: 0;
    width: 50px; height: 30px;
    background: var(--chip);
  }

  /* Back */
  .back-name {
    position: absolute;
    inset: 0;
    display: flex;
    align-items: center;
    justify-content: center;
    gap: 16px;
  }
  .back-name__dot {
    width: 44px; height: 44px;
    border-radius: 50%;
    background: var(--brand-blue-deep);
  }
  .back-name__text {
    font-weight: 700;
    font-size: 30px;
    color: var(--brand-blue-deep);
    text-transform: uppercase;
    line-height: 1.15;
    letter-spacing: 0.5px;
  }
</style>
</head>
<body>

<section class="card card--front" aria-label="Business card front">
  <div class="company">
    <span class="company__dot"></span>
    <div class="company__name">Quarrow<br>Signal Instruments</div>
  </div>

  <div class="person">
    <div class="person__name">Marlene</div>
    <div class="person__title">Director</div>
  </div>
  <div class="divider"></div>

  <ul class="contacts">
    <li>
      <svg viewBox="0 0 12 12" aria-hidden="true"><path d="M3 1l2 2-1 1.5a6 6 0 0 0 3.5 3.5L9 7l2 2-1.5 1.8C5 10.5 1.5 7 1.2 2.5z" fill="var(--brand-blue)"/></svg>
      +001 555 210 4832
    </li>
    <li>
      <svg viewBox="0 0 12 12" aria-hidden="true"><rect x="1" y="3" width="10" height="8" rx="1" fill="var(--brand-blue)"/><rect x="3" y="1" width="6" height="3" fill="var(--brand-blue)"/></svg>
      +001 555 210 7719
    </li>
    <li>
      <svg viewBox="0 0 12 12" aria-hidden="true"><circle cx="6" cy="6" r="5" fill="none" stroke="var(--brand-blue)" stroke-width="1.4"/><path d="M1 6h10M6 1c-2.5 3-2.5 7 0 10M6 1c2.5 3 2.5 7 0 10" fill="none" stroke="var(--brand-blue)" stroke-width="1"/></svg>
      www.quarrowsignal.com
    </li>
    <li>
      <svg viewBox="0 0 12 12" aria-hidden="true"><rect x="1" y="2.5" width="10" height="7" rx="1" fill="var(--brand-blue)"/><path d="M1.5 3l4.5 3.5L10.5 3" fill="none" stroke="var(--card-dark)" stroke-width="1"/></svg>
      info@quarrowsignal.com
    </li>
  </ul>

  <div class="address-band">
    1850 Kestrel Park Road • Alderton, CO 80611
    <span class="address-band__chip"></span>
  </div>
</section>

<section class="card card--back" aria-label="Business card back">
  <div class="back-name">
    <span class="back-name__dot"></span>
    <div class="back-name__text">Quarrow<br>Signal Instruments</div>
  </div>
</section>

</body>
</html>
```